HOT TUB - SPAS service needs an business card

I need an business for my company who his specialise in a maintenance,water treatment and cleaning of Hot Tub - Spas for commercial and residential customers. The company operate mainly in the ski resort of Chamonix, Megève and St Gervais. The final product should communicate pure water, cleanest and professional for luxury property's.
I have upload a logo but any improvement on it is welcome.(color,size, details etc..) or any other idea. Thank you
Company Name: 58 BAINS
My name: Lucien Marchetti
Email: lucimarch@examplemail.net
Tel: +33 (0)6 71 58 29 64
Description to be on the card in french(first langage) and in English:
- Spas service
- Entretien, traitement eau, nettoyage.
- Maintenance, water treatment, cleaning.
Industry/Entity Type
Residential
Colors
Designer to choose colors to be used in the design.
Look and feel
Each slider illustrates characteristics of the customer's brand and the style your logo design should communicate.

```html
<!DOCTYPE html>
<html lang="fr">
<head>
<meta charset="utf-8">
<title>58 BAINS – Business card</title>
<link href="https://fonts.googleapis.com/css2?family=Source+Sans+3:wght@400;600;700&display=swap" rel="stylesheet">
<style>
  :root {
    --backdrop: #e9edf1;
    --card-blue: #22a6ff;
    --band-blue: #0b72d4;
    --notch-blue: #1e98f2;
    --ink: #ffffff;
    --mark-fill: #4ab6ff;
  }
  * { margin: 0; padding: 0; box-sizing: border-box; }
  html, body {
    width: 1200px; height: 1139px; overflow: hidden;
    background: var(--backdrop);
    font-family: "Source Sans 3", "Myriad Pro", Arial, sans-serif;
    color: var(--ink);
  }
  .canvas { position: relative; width: 1200px; height: 1139px; }
  .card {
    position: absolute; width: 890px; height: 510px;
    background: var(--card-blue); overflow: hidden;
  }
  .card--front { left: 29px; top: 29px; }
  .card--back { left: 275px; top: 584px; width: 892px; }

  .front-band { position: absolute; inset: 0; }

  .brand-mark {
    position: absolute; display: flex; align-items: center; gap: 18px;
    font-weight: 600; letter-spacing: 1px;
  }
  .brand-mark__square { width: 22px; height: 22px; background: var(--ink); }
  .card--front .brand-mark { left: 200px; top: 95px; font-size: 64px; }
  .card--back .brand-mark { left: 50%; top: 150px; transform: translateX(-50%); font-size: 76px; }

  .company-name {
    position: absolute; left: 165px; top: 245px;
    font-size: 42px; font-weight: 600; line-height: 1;
  }
  .holder-name {
    position: absolute; left: 175px; top: 327px;
    font-size: 36px; font-weight: 700; line-height: 1;
  }
  .contact {
    position: absolute; left: 175px; display: flex; align-items: center; gap: 12px;
    font-size: 28px; line-height: 1;
  }
  .contact--phone { top: 400px; font-weight: 600; }
  .contact--email { top: 452px; }
  .contact svg { width: 26px; height: 26px; flex: none; }

  .services {
    position: absolute; left: 0; right: 0; top: 348px; text-align: center;
  }
  .services__title { font-size: 31px; font-weight: 600; line-height: 1; margin-bottom: 12px; }
  .services__line { font-size: 30px; line-height: 42px; word-spacing: 2px; }
  .services__line span { margin: 0 6px; }
</style>
</head>
<body>
<main class="canvas">

  <section class="card card--front" aria-label="Recto de la carte">
    <svg class="front-band" width="890" height="510" viewBox="0 0 890 510" aria-hidden="true">
      <rect x="0" y="0" width="143" height="510" fill="var(--band-blue)"/>
      <polygon points="49,214 143,60 143,214" fill="var(--notch-blue)"/>
      <rect x="143" y="0" width="3" height="210" fill="var(--ink)"/>
      <rect x="143" y="225" width="3" height="285" fill="var(--ink)"/>
      <rect x="76" y="197" width="552" height="3" fill="var(--ink)"/>
    </svg>
    <div class="brand-mark"><span class="brand-mark__square"></span>58 BAINS</div>

    <h1 class="company-name">58 BAINS</h1>
    <p class="holder-name">Lucien Marchetti</p>
    <p class="contact contact--phone">
      <svg viewBox="0 0 24 24" aria-hidden="true"><circle cx="12" cy="12" r="10.5" fill="none" stroke="#fff" stroke-width="1.6"/><path d="M8.5 6.5c-1.5 1-1.7 3.3.2 6.2s4 4.3 5.8 4.1l1.3-1.7-2.3-1.9-1.2.8c-.9-.5-2.2-2.1-2.6-3.1l.9-1.1-1.5-2.6z" fill="#fff"/></svg>
      +33 (0)6 71 58 29 64
    </p>
    <p class="contact contact--email">
      <svg viewBox="0 0 24 24" aria-hidden="true"><rect x="2" y="6" width="20" height="13" fill="#fff"/><path d="M2 6l10 7 10-7" fill="none" stroke="var(--card-blue)" stroke-width="1.8"/></svg>
      lucimarch@examplemail.net
    </p>
  </section>

  <section class="card card--back" aria-label="Verso de la carte">
    <div class="brand-mark"><span class="brand-mark__square"></span>58 BAINS</div>
    <div class="services">
      <h2 class="services__title">SPAS SERVICES</h2>
      <p class="services__line"><span>• Entretien</span><span>• traitement eau</span><span>• nettoyage</span></p>
      <p class="services__line"><span>• Maintenance</span><span>• water treatment</span><span>• cleaning.</span></p>
    </div>
  </section>

</main>
</body>
</html>
```